Weightloss company needs Business Card

We want a business card that is clean and professional, yet portrays that we are a friendly, innovative, and versatile program designed to fit the needs of our clients.
I would like there to be 2 sides, one side having an appointment card, and the other side containing the logo and business information. There can be decorations on both sides. The logo is attached.

Target Market(s)

Men and women 40-60

Industry/Entity Type

Business

Contact Information for Business Card

Font styles to use
Sans Serif

Requirements
Must have
• The logo, space for business information
Nice to have
• The colors in the logo
Should not have
• No pictures of people or food

```html
<!DOCTYPE html>
<html lang="en">
<head>
<meta charset="utf-8">
<title>Renew Turn Wellness – Business Card</title>
<link href="https://fonts.googleapis.com/css2?family=Montserrat:wght@400;500;700&display=swap" rel="stylesheet">
<style>
  :root {
    --bg: #2b2b2d;
    --card: #ffffff;
    --brand-red: #e8213a;
    --brand-blue: #4cc6ef;
    --ink: #1f1f1f;
    --rule: #2a2a2a;
    --on-blue: #ffffff;
  }
  * { box-sizing: border-box; margin: 0; padding: 0; }
  html, body {
    width: 1200px; height: 900px; overflow: hidden;
    background: var(--bg);
    font-family: "Montserrat", Arial, sans-serif;
  }
  .canvas { position: relative; width: 1200px; height: 900px; }
  .card {
    position: absolute; width: 560px; height: 320px;
    background: var(--card); border-radius: 22px; overflow: hidden;
    box-shadow: 0 18px 40px rgba(0,0,0,.45);
  }
  .card--appointment { left: 80px; top: 100px; }
  .card--contact { left: 560px; top: 480px; }

  .brand {
    position: absolute; display: flex; align-items: center; gap: 10px;
    color: var(--brand-red); font-weight: 700; line-height: 1.05;
    font-size: 25px; letter-spacing: .2px;
  }
  .brand__dot {
    width: 16px; height: 16px; border-radius: 50%; background: var(--brand-red); flex: none;
  }
  .card--appointment .brand { left: 44px; top: 70px; }
  .card--contact .brand { left: 44px; top: 62px; }

  .appointment__title {
    position: absolute; left: 44px; top: 160px;
    color: var(--brand-red); font-size: 14px; letter-spacing: .5px;
  }
  .appointment__lines { position: absolute; left: 44px; right: 40px; top: 30px; }
  .field {
    position: absolute; display: flex; align-items: flex-end; gap: 10px;
    font-size: 15px; color: var(--ink);
  }
  .field__rule { flex: 1; border-bottom: 1.4px solid var(--rule); height: 1px; }
  .field--blank { left: 250px; right: 44px; top: 78px; height: 20px; }
  .field--name { left: 44px; right: 44px; top: 190px; }
  .field--date { left: 44px; right: 44px; top: 230px; }
  .field--time { left: 44px; right: 44px; top: 270px; }

  .band {
    position: absolute; left: 0; right: 0; top: 168px; height: 118px;
    background: var(--brand-blue);
  }
  .person {
    position: absolute; left: 44px; top: 140px; text-align: right; width: 230px;
  }
  .person__name {
    color: var(--brand-red); font-weight: 700; font-size: 25px; letter-spacing: .3px;
  }
  .person__role { color: var(--on-blue); font-size: 13px; margin-top: 6px; }
  .person__address { color: var(--on-blue); font-size: 14px; margin-top: 12px; line-height: 1.45; }

  .contact-list {
    position: absolute; left: 300px; top: 192px; list-style: none;
    color: var(--on-blue); font-size: 13.5px;
  }
  .contact-list li { display: flex; align-items: center; gap: 10px; margin-bottom: 9px; }
  .contact-list svg { width: 14px; height: 14px; flex: none; }
</style>
</head>
<body>
<main class="canvas">

  <section class="card card--appointment" aria-label="Appointment side">
    <div class="brand"><span class="brand__dot"></span><span>Renew Turn<br>Wellness</span></div>
    <div class="field field--blank"><span class="field__rule"></span></div>
    <p class="appointment__title">APPOINTMENT</p>
    <div class="field field--name"><span>Name:</span><span class="field__rule"></span></div>
    <div class="field field--date"><span>Date:</span><span class="field__rule"></span></div>
    <div class="field field--time"><span>Time:</span><span class="field__rule"></span></div>
  </section>

  <section class="card card--contact" aria-label="Contact side">
    <div class="brand"><span class="brand__dot"></span><span>Renew Turn<br>Wellness</span></div>
    <div class="band"></div>
    <div class="person">
      <p class="person__name">MARLON AVERY</p>
      <p class="person__role">DIRECTOR</p>
      <p class="person__address">Cedar Lane, 30517<br>Harbor City, Westland</p>
    </div>
    <ul class="contact-list">
      <li>
        <svg viewBox="0 0 24 24" aria-hidden="true"><path fill="#e8213a" d="M6.6 10.8a15 15 0 0 0 6.6 6.6l2.2-2.2a1 1 0 0 1 1-.25 11.4 11.4 0 0 0 3.6.57 1 1 0 0 1 1 1V20a1 1 0 0 1-1 1A17 17 0 0 1 3 4a1 1 0 0 1 1-1h3.5a1 1 0 0 1 1 1c0 1.25.2 2.45.57 3.57a1 1 0 0 1-.25 1z"/></svg>
        +330 2715-4803
      </li>
      <li>
        <svg viewBox="0 0 24 24" aria-hidden="true"><rect x="3" y="5" width="18" height="14" rx="1.5" fill="none" stroke="#e8213a" stroke-width="2"/><path d="M3 6l9 7 9-7" fill="none" stroke="#e8213a" stroke-width="2"/></svg>
        info@renewturnwellness.com
      </li>
      <li>
        <svg viewBox="0 0 24 24" aria-hidden="true"><circle cx="12" cy="12" r="9" fill="none" stroke="#e8213a" stroke-width="2"/><path d="M3 12h18M12 3c3 3.5 3 14.5 0 18M12 3c-3 3.5-3 14.5 0 18" fill="none" stroke="#e8213a" stroke-width="1.6"/></svg>
        www.renewturnwellness.com
      </li>
    </ul>
  </section>

</main>
</body>
</html>
```